Business Card for Professional Photographer

I'm looking for an eye catching modern clean design that compliments my logo/ website fonts & colours.
I specialise in architecture, corporate & commercial photography so I'm marketing to professional clients rather than portrait / wedding clients.

I would prefer to not have a solid black design.

My logo brand guide is as follows :

Main front font. : Reislust
Main font colour : #fff
Slogan front font : Ubuntu Bold
Monogram front font : Venti Medium
Container colour : #fff

I need print ready files in pdf .png & .eps formats.

Included in the files below are some screen grabs as reference to font & colours etc.

```html
<!DOCTYPE html>
<html lang="en">
<head>
<meta charset="utf-8">
<title>Clear Frame – Business Card</title>
<link rel="stylesheet" href="https://fonts.googleapis.com/css2?family=Josefin+Sans:wght@300;400&family=Ubuntu:ital,wght@0,400;1,700&family=Roboto:wght@400&display=swap">
<style>
  :root {
    --backdrop: #3a3a3c;
    --backdrop-deep: #252527;
    --card: #1d1d1f;
    --card-edge: #141415;
    --gold-dark: #a9822f;
    --gold-mid: #d9b458;
    --gold-light: #f4dc8f;
    --ink-white: #f2f2f2;
    --ink-dark: #2a2418;
  }
  * { margin: 0; padding: 0; box-sizing: border-box; }
  html, body { width: 799px; height: 1200px; overflow: hidden; }
  body {
    background: radial-gradient(ellipse at 50% 45%, var(--backdrop) 0%, var(--backdrop-deep) 100%);
    position: relative;
    font-family: "Roboto", sans-serif;
  }
  .card {
    position: absolute;
    left: 70px;
    width: 660px;
    height: 377px;
    background: linear-gradient(160deg, #232325 0%, var(--card) 60%, var(--card-edge) 100%);
    border-radius: 4px;
    box-shadow: 0 18px 40px rgba(0,0,0,.55);
    overflow: hidden;
  }
  .card--front { top: 150px; }
  .card--back { top: 680px; }

  .gold-text {
    background: linear-gradient(100deg, var(--gold-dark) 0%, var(--gold-light) 45%, var(--gold-mid) 70%, var(--gold-dark) 100%);
    -webkit-background-clip: text;
    background-clip: text;
    color: transparent;
  }

  /* Front */
  .front-brand {
    position: absolute;
    left: 0; right: 0; top: 120px;
    display: flex; align-items: center; justify-content: center; gap: 18px;
  }
  .brand-dot {
    width: 34px; height: 34px; border-radius: 50%;
    border: 4px solid var(--gold-mid);
  }
  .front-brand .brand-name {
    font-family: "Josefin Sans", sans-serif;
    font-weight: 400;
    font-size: 50px;
    letter-spacing: 8px;
  }
  .front-web {
    position: absolute;
    left: 0; right: 0; top: 290px;
    text-align: center;
    font-family: "Josefin Sans", sans-serif;
    font-size: 16px;
    letter-spacing: 4px;
  }

  /* Back */
  .back-brand { position: absolute; left: 32px; top: 36px; }
  .back-brand .brand-row { display: flex; align-items: center; gap: 14px; }
  .back-brand .brand-dot { width: 26px; height: 26px; border-width: 3px; }
  .back-brand .brand-name {
    font-family: "Josefin Sans", sans-serif;
    font-weight: 300;
    font-size: 36px;
    letter-spacing: 6px;
  }
  .back-brand .slogan {
    margin-top: 4px; margin-left: 40px;
    font-family: "Ubuntu", sans-serif;
    font-weight: 700;
    font-size: 11px;
    letter-spacing: 3.2px;
  }
  .person { position: absolute; left: 32px; top: 140px; }
  .person .name {
    font-family: "Ubuntu", sans-serif;
    font-style: italic; font-weight: 700;
    font-size: 22px;
  }
  .person .role { color: var(--ink-white); font-size: 15px; margin-top: 2px; }

  .contact {
    position: absolute; left: 372px; top: 188px;
    list-style: none;
  }
  .contact li {
    display: flex; align-items: center; gap: 12px;
    color: var(--ink-white); font-size: 16px; line-height: 25px;
  }
  .contact svg { width: 14px; height: 14px; flex: none; }

  .address-band {
    position: absolute; left: 0; bottom: 0;
    width: 660px; height: 56px;
    background: linear-gradient(100deg, var(--gold-dark) 0%, var(--gold-mid) 40%, var(--gold-light) 70%, var(--gold-mid) 100%);
    display: flex; align-items: center; justify-content: flex-end;
    padding-right: 34px;
  }
  .address { font-size: 16px; color: var(--ink-dark); }
</style>
</head>
<body>
  <svg width="0" height="0" style="position:absolute" aria-hidden="true">
    <defs>
      <linearGradient id="gold" x1="0" y1="0" x2="1" y2="0.3">
        <stop offset="0" stop-color="#a9822f"/>
        <stop offset="0.5" stop-color="#e8c871"/>
        <stop offset="0.8" stop-color="#f4dc8f"/>
        <stop offset="1" stop-color="#c69c45"/>
      </linearGradient>
    </defs>
  </svg>

  <section class="card card--front" aria-label="Card front">
    <div class="front-brand">
      <span class="brand-dot"></span>
      <span class="brand-name gold-text">CLEAR FRAME</span>
    </div>
    <p class="front-web gold-text">www.clearframe.com.au</p>
  </section>

  <section class="card card--back" aria-label="Card back">
    <div class="back-brand">
      <div class="brand-row">
        <span class="brand-dot"></span>
        <span class="brand-name gold-text">CLEAR FRAME</span>
      </div>
      <p class="slogan gold-text">Architecture Corporate Commercial</p>
    </div>

    <div class="person">
      <p class="name gold-text">Reid Calder</p>
      <p class="role">Photographer</p>
    </div>

    <ul class="contact">
      <li>
        <svg viewBox="0 0 14 14"><path fill="url(#gold)" d="M3 1l2.2 2.6-1.2 1.6c.9 1.9 2.3 3.3 4.2 4.2l1.6-1.2L12.4 10.4 11 12.6C6 12.3 1.7 8 1.4 3z"/></svg>
        0400 187 265
      </li>
      <li>
        <svg viewBox="0 0 14 14"><rect x="1" y="3" width="12" height="8" fill="url(#gold)"/><path d="M1 3l6 4.5L13 3" fill="none" stroke="#1d1d1f" stroke-width="1"/></svg>
        hello@clearframe.com.au
      </li>
      <li>
        <svg viewBox="0 0 14 14"><circle cx="7" cy="7" r="6" fill="url(#gold)"/><path d="M1 7h12M7 1c-2.5 3-2.5 9 0 12M7 1c2.5 3 2.5 9 0 12" fill="none" stroke="#1d1d1f" stroke-width=".8"/></svg>
        www.clearframe.com.au
      </li>
    </ul>

    <div class="address-band">
      <p class="address">48 Harbour Rd Westvale Vic 3999</p>
    </div>
  </section>
</body>
</html>
```